Swing Dance Themed Cleaning Company Website

We need a website designed for a cleaning company based in Portland, Oregon called Foxtrot Lane. We clean homes and commercial buildings, inside and out.

needs to be vintage and like the velvet tambour. Speakeasy 1920s feel.
needs to be classy.

Check out foxtrotlane.com We are not happy with the site currently.

please look at house scout site for more content https://www.housescoutpro.com/rated.FoxtrotLaneCleaning.48217705.html

Check out my videos on my ClipHaven channel Foxtrot Lane

Target Market(s)

middle class and home owner

Industry/Entity Type

Cleaning Service

Number of Pages Required

3 page

Font styles to use
Other font styles liked:
• jazzrag

Colors

Designer to choose colors to be used in the design.

Requirements
Must have
• must be good on pc and mobile

```html
<!DOCTYPE html>
<html lang="en">
<head>
<meta charset="utf-8">
<title>Foxtrot Lane — Cleaning Services Portland</title>
<link href="https://fonts.googleapis.com/css2?family=Limelight&family=Oswald:wght@400;600;700&family=Open+Sans:wght@400;600;700&display=swap" rel="stylesheet">
<style>
:root{
  --yellow:#f7ec1b;
  --yellow-deep:#efe10f;
  --ink:#1c1c1c;
  --panel:#2b2b2b;
  --paper:#e8e6dd;
  --grey-text:#5a5a5a;
  --white:#ffffff;
}
*{box-sizing:border-box;margin:0;padding:0}
html,body{width:1200px;height:4444px;overflow:hidden}
body{background:var(--paper);font-family:"Open Sans",Arial,sans-serif;color:var(--ink)}
.page{position:relative;width:1200px;height:4444px}
section,header{position:relative;width:1200px}
.bg{position:absolute;inset:0;width:100%;height:100%;z-index:0}
.inner{position:relative;z-index:1}

/* nav */
.site-nav{height:100px;background:var(--yellow);border-bottom:2px solid var(--yellow-deep);z-index:5}
.nav-list{list-style:none;font-family:"Oswald",sans-serif;font-weight:700;font-size:15px;letter-spacing:1px;text-transform:uppercase}
.nav-list li{position:absolute;top:38px}
.brand{position:absolute;left:500px;top:0;width:200px;height:100px;background:var(--ink);display:flex;flex-direction:column;align-items:center;justify-content:center;gap:6px}
.brand-name{font-family:"Oswald",sans-serif;font-weight:600;font-size:26px;color:var(--yellow);letter-spacing:2px;text-transform:uppercase;display:flex;align-items:center;gap:10px}
.brand-name .mark{width:14px;height:14px;background:var(--yellow)}
.brand-tag{font-family:"Oswald",sans-serif;font-size:10px;color:var(--yellow);letter-spacing:1px}

/* deco heading */
.deco-title{display:flex;align-items:center;justify-content:center;gap:16px}
.deco-title .rule{width:130px;height:2px;background:var(--ink)}
.deco-title .gem{width:14px;height:14px;border:2px solid var(--ink);transform:rotate(45deg)}
.deco-title h1,.deco-title h2{font-family:"Limelight",serif;font-weight:400;color:var(--yellow);-webkit-text-stroke:4px var(--ink);paint-order:stroke fill;text-transform:uppercase;letter-spacing:4px;line-height:1.1;padding:0 6px}
.deco-title h1{font-size:86px}
.deco-title h2{font-size:60px}
.on-dark .rule{background:var(--yellow)}
.on-dark .gem{border-color:var(--yellow)}
.on-dark h2{-webkit-text-stroke:0;color:var(--yellow)}

/* hero */
.hero{height:1000px}
.hero .inner{padding-top:70px;text-align:center}
.hero-lede{margin:30px auto 0;width:640px;font-size:20px;line-height:1.45;color:#333}
.showcase{position:absolute;left:167px;top:300px;width:866px;height:520px;background:var(--panel);clip-path:polygon(50px 0,816px 0,866px 50px,866px 100%,0 100%,0 50px)}
.showcase-photo{position:absolute;left:62px;top:34px;width:742px;height:360px;background:linear-gradient(135deg,#c9c6c0 0%,#dcd9d4 45%,#b9c9b6 70%,#c7b9b6 100%)}
.showcase-caption{position:absolute;left:150px;right:150px;top:418px;font-size:14px;line-height:1.6;color:#cfcfcf;text-align:center}
.dots{position:absolute;left:0;right:0;top:482px;display:flex;justify-content:center;gap:8px}
.dots span{width:12px;height:12px;background:#bbb}
.dots span.on{background:var(--yellow)}
.quote-tab{position:absolute;left:450px;top:820px;width:300px;height:76px;background:var(--yellow);clip-path:polygon(0 0,100% 0,100% 55%,50% 100%,0 55%);font-family:"Oswald",sans-serif;font-weight:700;font-size:17px;letter-spacing:1px;text-align:center;padding-top:16px}

/* about */
.about{height:420px;text-align:center}
.about .inner{padding-top:10px}
.about h3{margin-top:24px;font-family:"Oswald",sans-serif;font-weight:600;font-size:26px}
.about p{width:760px;margin:16px auto 0;font-size:15px;line-height:1.7;color:var(--grey-text)}
.btn-row{display:flex;justify-content:center;gap:20px;margin-top:26px}
.btn-outline{padding:10px 18px;border:1px solid var(--ink);font-size:13px;font-weight:600}
.about-link{display:inline-block;margin-top:30px;font-family:"Oswald",sans-serif;font-weight:700;font-size:24px;text-decoration:underline}

/* services */
.services{height:1150px}
.services .inner{padding-top:150px}
.service-grid{display:grid;grid-template-columns:480px 480px;column-gap:60px;row-gap:60px;margin:70px 0 0 170px}
.service h4{font-family:"Oswald",sans-serif;font-weight:700;font-size:22px;text-transform:uppercase;margin-bottom:18px}
.service-body{display:flex;align-items:center;gap:26px}
.hex{width:190px;height:214px;clip-path:polygon(50% 0,100% 25%,100% 75%,50% 100%,0 75%,0 25%);flex:none}
.hex-house{background:linear-gradient(160deg,#7fa7c8,#d9c98a 60%,#b24a6a)}
.hex-move{background:linear-gradient(160deg,#bcd3e4,#e6e6e6 55%,#8c8c8c)}
.hex-exterior{background:linear-gradient(160deg,#2f5f8a,#8fb9d8 55%,#3c4f63)}
.hex-event{background:linear-gradient(160deg,#5c3b5e,#b27b4c 55%,#2e2a3c)}
.service ul{list-style:none;font-size:15px;line-height:1.9}
.service li::before{content:"•";margin-right:8px}

/* blog */
.blog{height:640px}
.blog .inner{padding-top:30px;text-align:center}
.blog .sub{margin-top:20px;font-family:"Oswald",sans-serif;font-weight:700;font-size:28px}
.posts{display:flex;gap:80px;justify-content:center;margin-top:40px;text-align:left}
.post{display:flex;gap:18px;width:430px}
.post-media{width:150px;flex:none;background:var(--white);padding-bottom:10px}
.post-photo{height:150px;position:relative}
.post-photo.fest{background:linear-gradient(150deg,#a23a3a,#d98a5a 55%,#4c6b3a)}
.post-photo.sponsor{background:linear-gradient(150deg,#d7b35a,#e58bb0 55%,#6aa0c8)}
.cam{position:absolute;left:61px;bottom:-14px;width:28px;height:28px;border-radius:50%;background:var(--yellow)}
.post-media .label{margin-top:22px;text-align:center;font-family:"Oswald",sans-serif;font-size:12px;letter-spacing:1px;text-transform:uppercase}
.post-text{display:grid;grid-template-columns:46px 1fr;column-gap:12px;align-content:start}
.post-text h5{grid-column:1/3;font-family:"Oswald",sans-serif;font-weight:700;font-size:18px;line-height:1.3}
.post-text .meta{grid-column:1/3;font-size:11px;color:var(--grey-text);margin:4px 0 10px}
.date{background:var(--ink);color:var(--white);text-align:center;font-family:"Oswald",sans-serif;font-size:13px;line-height:1.2;padding:6px 0;height:54px}
.post-text p{font-size:12px;line-height:1.55;color:var(--grey-text)}
.more{grid-column:2;margin-top:8px;font-size:12px;font-weight:700;text-decoration:underline}
.btn-view{display:inline-block;margin-top:60px;padding:10px 18px;border:1px solid var(--ink);background:var(--white);font-size:13px;font-weight:600}

/* contact */
.contact{height:1134px;background:var(--ink);color:var(--white)}
.contact .inner{padding-top:170px}
.contact-lede{width:820px;margin:36px auto 0;text-align:center;font-weight:700;font-size:26px;line-height:1.4}
.contact-body{display:flex;gap:40px;margin:80px 0 0 180px}
.contact-form{width:420px;display:flex;flex-direction:column;gap:16px}
.field{background:var(--white);height:46px;color:#888;font-size:12px;padding:15px 14px}
.field.message{height:130px}
.btn-submit{width:110px;height:46px;background:var(--yellow);color:var(--ink);font-family:"Oswald",sans-serif;font-weight:600;font-size:14px;display:flex;align-items:center;justify-content:center;margin-top:10px}
.contact-info{width:420px;border-left:1px solid #444;padding-left:20px}
.info-row{display:flex;align-items:center;gap:12px;margin-bottom:26px;font-size:14px}
.info-row svg{flex:none}
.info-row b{font-family:"Oswald",sans-serif;font-weight:600;letter-spacing:1px;margin-right:14px}
.social{display:flex;gap:14px;margin-top:20px;list-style:none}
.social li{width:70px;height:70px;border-radius:50%;background:var(--yellow);color:var(--ink);display:flex;align-items:center;justify-content:center;font-family:"Oswald",sans-serif;font-weight:600;font-size:11px;letter-spacing:.5px}
.copyright{margin-top:24px;font-size:12px;color:#bbb}
</style>
</head>
<body>
<div class="page">

  <header class="site-nav">
    <ul class="nav-list">
      <li style="left:150px">Home</li>
      <li style="left:250px">Contact Us</li>
      <li style="left:385px">About Us</li>
      <li style="left:760px">Services</li>
      <li style="left:880px">Blog</li>
      <li style="left:975px">Search</li>
    </ul>
    <div class="brand">
      <div class="brand-name"><span class="mark"></span>Foxtrot Lane</div>
      <div class="brand-tag">HOME · CLEANING · CLASSY · PORTLAND</div>
    </div>
  </header>

  <section class="hero">
    <svg class="bg" viewBox="0 0 1200 1000" preserveAspectRatio="none">
      <rect width="1200" height="1000" fill="#f7ec1b"/>
      <polygon points="0,440 600,700 1200,440 1200,1000 0,1000" fill="#e8e6dd"/>
    </svg>
    <div class="inner">
      <div class="deco-title"><span class="rule"></span><span class="gem"></span><h1>Foxtrot Lane</h1><span class="gem"></span><span class="rule"></span></div>
      <p class="hero-lede">Foxtrot Lane is a locally owned family business dedicated to providing you with quality cleaning services for a reasonable price.</p>
    </div>
    <div class="showcase">
      <div class="showcase-photo" role="img" aria-label="Photo of a smiling retro-styled cleaner holding a yellow cloth and wearing pink gloves"></div>
      <p class="showcase-caption">Foxtrot Lane is a family owned professional cleaning business. We provide our years of cleaning experience to homes and businesses in and around Portland, Oregon.</p>
      <div class="dots"><span></span><span></span><span class="on"></span></div>
    </div>
    <div class="quote-tab">GET A QUOTE TODAY</div>
  </section>

  <section class="about">
    <div class="inner">
      <div class="deco-title"><span class="rule"></span><span class="gem"></span><h2>About Us</h2><span class="gem"></span><span class="rule"></span></div>
      <h3>Making the Greater Portland Area Clean, One Building at a Time</h3>
      <p>Foxtrot Lane is a locally owned family business dedicated to providing you with quality cleaning services for a reasonable price. We provide flexible 24 hour service and we are available for cleaning emergencies.</p>
      <div class="btn-row"><span class="btn-outline">Learn More</span><span class="btn-outline">Leave a Review</span></div>
      <span class="about-link">CLEANING AND MAINTENANCE</span>
    </div>
  </section>

  <section class="services">
    <svg class="bg" viewBox="0 0 1200 1150" preserveAspectRatio="none">
      <polygon points="0,0 600,110 1200,0 1200,950 600,1150 0,950" fill="#f7ec1b"/>
    </svg>
    <div class="inner">
      <div class="deco-title"><span class="rule"></span><span class="gem"></span><h2>Our Services</h2><span class="gem"></span><span class="rule"></span></div>
      <div class="service-grid">
        <div class="service">
          <h4>General House Keeping</h4>
          <div class="service-body">
            <div class="hex hex-house" role="img" aria-label="Photo of a cleaner tidying a living room"></div>
            <ul><li>Floor to ceiling dusting</li><li>Cobweb removal</li><li>Kitchen cleaning</li><li>Bathroom cleaning</li><li>Sweep, mop and vacuum floors</li></ul>
          </div>
        </div>
        <div class="service">
          <h4>Move Outs &amp; Detail</h4>
          <div class="service-body">
            <div class="hex hex-move" role="img" aria-label="Photo of a house exterior being washed"></div>
            <ul><li>Leaf blowing</li><li>Pressure washing</li><li>Window washing</li><li>Exterior house detail</li><li>Gutter cleaning</li></ul>
          </div>
        </div>
        <div class="service">
          <h4>Exterior Services</h4>
          <div class="service-body">
            <div class="hex hex-exterior" role="img" aria-label="Photo of window washers on a glass building"></div>
            <ul><li>All general house keeping</li><li>Make your house 'move in' ready</li><li>Refrigerator and oven cleaning</li><li>Window washing</li><li>Carpet cleaning</li></ul>
          </div>
        </div>
        <div class="service">
          <h4>Event Services</h4>
          <div class="service-body">
            <div class="hex hex-event" role="img" aria-label="Photo of an evening event venue"></div>
            <ul><li>Event hosting at the Alder Street studio</li><li>Event cleanup</li></ul>
          </div>
        </div>
      </div>
    </div>
  </section>

  <section class="blog">
    <div class="inner">
      <div class="deco-title"><span class="rule"></span><span class="gem"></span><h2>Latest Blog</h2><span class="gem"></span><span class="rule"></span></div>
      <p class="sub">The latest news from Foxtrot Lane</p>
      <div class="posts">
        <article class="post">
          <div class="post-media"><div class="post-photo fest" role="img" aria-label="Photo of a crowd at a summer music festival"><span class="cam"></span></div><div class="label">Foxtrot Lane</div></div>
          <div class="post-text">
            <h5>Foxtrot Lane Returns to Riverside Rhythm Festival 2017</h5>
            <div class="meta">Posted in Events by Ellis Marlow on July 15, 2017</div>
            <div class="date">15<br>July</div>
            <p>Foxtrot Lane returns to the Riverside Rhythm Festival this June 30 through July 4, 2017. Say hello to our crew there.</p>
            <span class="more">Learn More</span>
          </div>
        </article>
        <article class="post">
          <div class="post-media"><div class="post-photo sponsor" role="img" aria-label="Photo of a festival guest in a bright sun hat"><span class="cam"></span></div><div class="label">Foxtrot Lane</div></div>
          <div class="post-text">
            <h5>Foxtrot Lane sponsoring Riverside Rhythm Fest 2018</h5>
            <div class="meta">Posted in Events by Ellis Marlow on May 16, 2018</div>
            <div class="date">16<br>May</div>
            <p>Foxtrot Lane will be sponsoring the Riverside Rhythm Fest. Find details at www.riversiderhythmfest.com</p>
            <span class="more">Learn More</span>
          </div>
        </article>
      </div>
      <span class="btn-view">View More Blogs</span>
    </div>
  </section>

  <section class="contact">
    <svg class="bg" viewBox="0 0 1200 1134" preserveAspectRatio="none">
      <polygon points="0,0 600,110 1200,0" fill="#e8e6dd"/>
    </svg>
    <div class="inner">
      <div class="deco-title on-dark"><span class="rule"></span><span class="gem"></span><h2>Contact Us</h2><span class="gem"></span><span class="rule"></span></div>
      <p class="contact-lede">Contact us for a quote, to book a cleaning, or for any other reason. We're looking forward to hearing from you!</p>
      <div class="contact-body">
        <div class="contact-form">
          <div class="field">Enter Your Name</div>
          <div class="field">Enter Your Mail</div>
          <div class="field">Select</div>
          <div class="field message">Message</div>
          <div class="btn-submit">Submit</div>
        </div>
        <div class="contact-info">
          <div class="info-row">
            <svg width="20" height="24" viewBox="0 0 20 24"><path d="M10 1a8 8 0 0 0-8 8c0 6 8 14 8 14s8-8 8-14a8 8 0 0 0-8-8z" fill="#ffffff"/><circle cx="10" cy="9" r="3" fill="#1c1c1c"/></svg>
            <span><b>ADDRESS</b>418 SE Alder St #210, Portland, OR 97214</span>
          </div>
          <div class="info-row">
            <svg width="20" height="22" viewBox="0 0 20 22"><path d="M4 1h4l2 5-3 2c1 3 3 5 6 6l2-3 5 2v4c0 2-2 3-4 3C8 20 0 12 0 5c0-2 2-4 4-4z" fill="#ffffff"/></svg>
            <span><b>PHONE</b>971-555-0148</span>
          </div>
          <div class="info-row">
            <svg width="22" height="16" viewBox="0 0 22 16"><rect width="22" height="16" fill="#ffffff"/><path d="M0 0l11 9 11-9" fill="none" stroke="#1c1c1c" stroke-width="2"/></svg>
            <span><b>E-mail</b>ellis@foxtrotlane.com</span>
          </div>
          <ul class="social" aria-label="Social links">
            <li>Friendly</li><li>Chirpline</li><li>ClipHaven</li><li>Circles</li>
          </ul>
          <p class="copyright">Copyright © 2018 Foxtrot Lane. All Rights Reserved</p>
        </div>
      </div>
    </div>
  </section>

</div>
</body>
</html>
```